Business card design for a dynamic IT consulting company

We need a business card design for a young firm, specialized in the Telecommunications/Consulting industry. The name of the company is Quindor and Partners Business Consulting Ltd. (Short name: Quindor and Partnes)
Quindor = solve read reverse, so we aim to be uncomplicated and solution-oriented. The small pipe in our logo is also related to the word solve. So we need a new business card design, which is simple, eye catching and something non traditional (I would probably prefer a square shaped design rather than a rectangle, but open for suggestions). Attached our logo.

Target Market(s)

Usually our customers are Tier1 Telecoms providers (Q-Netra, Palorix, etc) and their executives.

Industry/Entity Type

Business

Contact Information for Business Card

Name: Bence Tolnavari
Email: b.tolnavari@quindor.hu
Web: www.quindor.hu
Mobile: +36 30 518 2769
Title: Managing Director

Optional:
Company name: Quindor and Partners Ltd.
Address: 1087 Budapest, Tolvenka str. 28/C, Hungary

Font styles to use
Other font styles liked:
• helveticaneue_medium, Prime Regular are used now.

Colors

Designer to choose colors to be used in the design.

Requirements
Must have
• I would like to have a 2 sided design.
Nice to have
• I thought if we make the logo a bit bigger (without the company name), that could go to the back with the company name below. I though, if the pipe in the logo is somehow touchable on the business card, would be nice and unique.

```html
<!DOCTYPE html>
<html lang="en">
<head>
<meta charset="utf-8">
<title>Quindor and Partners – Business Card</title>
<link rel="stylesheet" href="https://fonts.googleapis.com/css2?family=Arimo:wght@400;700&display=swap">
<style>
  :root {
    --backdrop: #7b5a3e;
    --card-dark: #5b5d60;
    --card-light: #f7f7f7;
    --brand-blue: #0a9ad8;
    --brand-grey: #5b5d60;
    --text-light: #ffffff;
  }
  html, body {
    margin: 0;
    padding: 0;
    overflow: hidden;
  }
  body {
    width: 1200px;
    height: 960px;
    background: var(--backdrop);
    position: relative;
    font-family: "Arimo", "Helvetica Neue", Arial, sans-serif;
  }
  .card {
    position: absolute;
    box-sizing: border-box;
    box-shadow: 2px 3px 6px rgba(0, 0, 0, 0.45);
  }
  .card--front {
    left: 200px;
    top: 306px;
    width: 343px;
    height: 341px;
    background: var(--card-dark);
    color: var(--text-light);
  }
  .card--back {
    left: 651px;
    top: 305px;
    width: 344px;
    height: 343px;
    background: var(--card-light);
  }
  .front-brand {
    position: absolute;
    left: 36px;
    top: 34px;
    display: flex;
    align-items: center;
    gap: 8px;
    font-size: 15px;
    font-weight: 400;
    color: var(--text-light);
  }
  .brand-square {
    width: 9px;
    height: 9px;
    background: var(--brand-blue);
  }
  .contact {
    position: absolute;
    left: 35px;
    top: 180px;
    font-size: 14px;
    line-height: 18px;
  }
  .contact__name {
    margin: 0;
    font-size: 18px;
    font-weight: 700;
    color: var(--brand-blue);
    line-height: 22px;
  }
  .contact__title {
    margin: 0 0 8px;
    font-size: 15px;
    line-height: 20px;
  }
  .contact__lines {
    margin: 0 0 10px;
  }
  .contact__label {
    color: var(--brand-blue);
    font-weight: 700;
  }
  .contact__address {
    margin: 0;
  }
  .back-brand {
    position: absolute;
    left: 0;
    right: 0;
    top: 120px;
    display: flex;
    flex-direction: column;
    align-items: center;
    gap: 18px;
  }
  .back-brand__square {
    width: 22px;
    height: 22px;
    background: var(--brand-blue);
  }
  .back-brand__name {
    font-size: 30px;
    font-weight: 400;
    color: var(--brand-grey);
    letter-spacing: 0.5px;
  }
  .web-band {
    position: absolute;
    left: 0;
    right: 0;
    top: 286px;
    height: 28px;
    background: var(--brand-blue);
    color: var(--text-light);
    font-size: 13px;
    line-height: 28px;
    letter-spacing: 7px;
    padding-left: 54px;
  }
</style>
</head>
<body>
  <section class="card card--front" aria-label="Business card front">
    <div class="front-brand"><span class="brand-square"></span>Quindor &amp; Partners</div>
    <div class="contact">
      <p class="contact__name">Bence Tolnavari</p>
      <p class="contact__title">Managing Director</p>
      <p class="contact__lines">
        <span class="contact__label">C:</span> +36 30 518 2769<br>
        <span class="contact__label">E:</span> b.tolnavari@quindor.hu
      </p>
      <p class="contact__address">
        Quindor and Partners Ltd., 1087 Budapest<br>
        Tolvenka str. 28/C, Hungary
      </p>
    </div>
  </section>

  <section class="card card--back" aria-label="Business card back">
    <div class="back-brand">
      <span class="back-brand__square"></span>
      <span class="back-brand__name">Quindor &amp; Partners</span>
    </div>
    <div class="web-band">www.quindor.hu</div>
  </section>
</body>
</html>
```